Global Consulting firm needs a Business Card Design (Contest)

We need a business card design for a company with global reach called 'Harborline Group'. Harborline Group is a Trusted Procurement Advisor that consults for Zenith 400 and Meridian 900 companies to find cost reductions in their spending. We would like to see designs that communicate fiduciary trust and sense of partnership. The Front should have our logo w/ 'trusted procurement advisor', Employee name and title, company address, email, phone and fax (logo attached "Harbor line group final"). The color scheme and basic concept should be consistent with our presentation front page (attached "HLG presentation cover page"). The Back should have our website (www.hlinellc.com) and an array of our areas of expertise: office supplies, lab supplies, wireless telecom, MRO and IT (see "lab supplies" file for example).

```html
<!DOCTYPE html>
<html lang="en">
<head>
<meta charset="utf-8">
<title>Harborline Group – Business Card</title>
<link rel="stylesheet" href="https://fonts.googleapis.com/css2?family=Sorts+Mill+Goudy:ital@0;1&family=Roboto:wght@400;500;700&display=swap">
<style>
  :root {
    --page-bg: #ecebe8;
    --card-bg: #ffffff;
    --map-tone: #ececec;
    --ink: #1c1c1c;
    --ink-soft: #2a2a2a;
    --gold: #c8961c;
    --navy: #1f3375;
    --tile-frame: #2b3f86;
    --divider: #d0d0d0;
  }
  * { box-sizing: border-box; margin: 0; padding: 0; }
  html, body { width: 1200px; height: 1000px; overflow: hidden; }
  body {
    background: var(--page-bg);
    position: relative;
    font-family: "Roboto", Arial, sans-serif;
    color: var(--ink);
  }
  .card {
    position: absolute;
    left: 265px;
    width: 665px;
    height: 396px;
    background: var(--card-bg);
    border-radius: 24px;
    box-shadow: 0 4px 12px rgba(0,0,0,0.18);
    overflow: hidden;
  }
  .card--front { top: 73px; }
  .card--back { top: 533px; }

  .world-map {
    position: absolute;
    border-radius: 40% 45% 35% 40%;
    background: radial-gradient(ellipse at center, var(--map-tone) 0%, rgba(236,236,236,0.6) 60%, rgba(255,255,255,0) 80%);
  }
  .card--front .world-map { left: 40px; top: 20px; width: 610px; height: 355px; }
  .card--back .world-map { left: 40px; top: 20px; width: 610px; height: 355px; }

  .brand {
    position: absolute;
    display: flex;
    align-items: center;
    gap: 12px;
  }
  .brand__mark {
    width: 40px; height: 40px;
    border-radius: 50%;
    background: var(--gold);
    flex: none;
  }
  .brand__name {
    font-family: "Sorts Mill Goudy", Georgia, serif;
    font-size: 31px;
    color: var(--ink);
    white-space: nowrap;
    letter-spacing: 0.2px;
  }
  .card--front .brand { left: 33px; top: 165px; }
  .tagline {
    position: absolute;
    left: 114px; top: 204px;
    font-family: "Sorts Mill Goudy", Georgia, serif;
    font-style: italic;
    font-size: 16px;
    color: var(--ink);
  }

  .divider {
    position: absolute;
    left: 398px; top: 88px;
    width: 2px; height: 210px;
    background: linear-gradient(to bottom, rgba(0,0,0,0), var(--divider) 20%, var(--divider) 80%, rgba(0,0,0,0));
    box-shadow: 3px 0 6px rgba(0,0,0,0.12);
  }

  .contact { position: absolute; left: 424px; top: 112px; }
  .contact__person { display: flex; align-items: flex-start; gap: 9px; margin-bottom: 20px; }
  .contact__name { font-size: 19px; font-weight: 700; color: var(--gold); line-height: 22px; }
  .contact__title { font-size: 17px; color: var(--ink-soft); line-height: 18px; }
  .contact__list { list-style: none; }
  .contact__item {
    display: flex; align-items: center; gap: 9px;
    font-size: 16px; line-height: 25px; color: var(--ink-soft);
  }
  .icon { width: 15px; height: 15px; flex: none; fill: var(--ink); }
  .contact__person .icon { margin-top: 6px; }

  .card--back .brand { left: 150px; top: 107px; }
  .website {
    position: absolute;
    left: 0; right: 0; top: 150px;
    text-align: center;
    padding-left: 22px;
    font-size: 18px;
    font-weight: 700;
    letter-spacing: 3.4px;
    color: var(--ink);
  }

  .expertise {
    position: absolute;
    top: 207px; left: 46px;
    display: flex;
    list-style: none;
  }
  .expertise__tile {
    position: relative;
    height: 78px;
    border: 1.5px solid var(--tile-frame);
    border-radius: 3px;
  }
  .expertise__label {
    position: absolute;
    top: -1px; left: 6px;
    background: var(--navy);
    color: #fff;
    font-size: 9px;
    font-weight: 500;
    padding: 1px 8px 2px;
    border-radius: 0 0 5px 5px;
    white-space: nowrap;
  }
  .expertise__photo { position: absolute; inset: 14px 3px 3px 3px; border-radius: 2px; }
  .photo--office { background: linear-gradient(135deg, #f4b8c4, #f6e27a 45%, #9fd2e8); }
  .photo--lab { background: linear-gradient(135deg, #dfe9f2, #c7d8ea 50%, #f0f3f6); }
  .photo--telecom { background: linear-gradient(135deg, #1d4e9c, #4f8fd6 55%, #a9c9ec); }
  .photo--mro { background: linear-gradient(135deg, #ffffff, #d4d6d8 50%, #f2f2f2); }
  .photo--shipping { background: linear-gradient(135deg, #b88a5a, #d7b48c 50%, #8c6a45); }
</style>
</head>
<body>

<section class="card card--front" aria-label="Business card front">
  <div class="world-map" role="img" aria-label="Faint grey world map in the background"></div>

  <div class="brand">
    <span class="brand__mark"></span>
    <span class="brand__name">Harborline Group</span>
  </div>
  <p class="tagline">Trusted Procurement Advisor</p>

  <div class="divider"></div>

  <div class="contact">
    <div class="contact__person">
      <svg class="icon" viewBox="0 0 16 16"><circle cx="8" cy="4.5" r="3.5"/><path d="M1 16c0-4 3-6.5 7-6.5s7 2.5 7 6.5z"/></svg>
      <div>
        <p class="contact__name">Paul Reyes</p>
        <p class="contact__title">Owner</p>
      </div>
    </div>
    <ul class="contact__list">
      <li class="contact__item">
        <svg class="icon" viewBox="0 0 16 16"><path d="M1 6c0-2 3-3.5 7-3.5s7 1.5 7 3.5v1.5h-3.5V5.5c-1-.4-2.2-.5-3.5-.5s-2.5.1-3.5.5v2H1z"/><path d="M4 9h8l1.5 5h-11z"/></svg>
        (855) 418 – 3092
      </li>
      <li class="contact__item">
        <svg class="icon" viewBox="0 0 16 16"><rect x="4" y="1" width="8" height="4"/><rect x="1" y="5.5" width="14" height="6" rx="1"/><rect x="4" y="10" width="8" height="5" fill="#fff" stroke="#1c1c1c" stroke-width="1.5"/></svg>
        (555) 612 – 0348
      </li>
      <li class="contact__item">
        <svg class="icon" viewBox="0 0 16 16"><path d="M1 3h14v10H1z"/><path d="M1 3l7 6 7-6" fill="none" stroke="#fff" stroke-width="1.3"/></svg>
        info@hlinellc.com
      </li>
      <li class="contact__item">
        <svg class="icon" viewBox="0 0 16 16"><path d="M8 0.5a5.5 5.5 0 0 0-5.5 5.5c0 4 5.5 9.5 5.5 9.5s5.5-5.5 5.5-9.5A5.5 5.5 0 0 0 8 0.5z"/><circle cx="8" cy="6" r="2.2" fill="#fff"/></svg>
        Linwood Bay, Delaware
      </li>
    </ul>
  </div>
</section>

<section class="card card--back" aria-label="Business card back">
  <div class="world-map" role="img" aria-label="Faint grey world map in the background"></div>

  <div class="brand">
    <span class="brand__mark"></span>
    <span class="brand__name">Harborline Group</span>
  </div>
  <p class="website">www.hlinellc.com</p>

  <ul class="expertise">
    <li class="expertise__tile" style="width:104px; margin-right:13px;">
      <div class="expertise__photo photo--office" role="img" aria-label="Photo of colourful sticky notes and paper clips"></div>
      <span class="expertise__label">Office Supplies</span>
    </li>
    <li class="expertise__tile" style="width:105px; margin-right:15px;">
      <div class="expertise__photo photo--lab" role="img" aria-label="Photo of laboratory test tubes and glassware"></div>
      <span class="expertise__label">Lab Supplies</span>
    </li>
    <li class="expertise__tile" style="width:105px; margin-right:16px;">
      <div class="expertise__photo photo--telecom" role="img" aria-label="Photo of a mobile phone held against a blue globe"></div>
      <span class="expertise__label">Wireless Telecom</span>
    </li>
    <li class="expertise__tile" style="width:98px; margin-right:13px;">
      <div class="expertise__photo photo--mro" role="img" aria-label="Photo of a wrench tightening a bolt"></div>
      <span class="expertise__label">MRO</span>
    </li>
    <li class="expertise__tile" style="width:105px;">
      <div class="expertise__photo photo--shipping" role="img" aria-label="Photo of a handheld scanner reading a parcel label"></div>
      <span class="expertise__label">Shipping/Postage</span>
    </li>
  </ul>
</section>

</body>
</html>
```